Modern Label for cleaning products for the brand Vorlix

We need a label design for our line of cleaning products. The label should feature our logo and an image to identify the product's intended use. I've added our logo and an image for use. This only concerns the design of the label on the front of the bottle.

Label dimensions:
Label 1 (500ml bottle with spray): width 58mm x height 115mm
Label 2: (1L bottle): width 73mm x height 140mm
The design must be consistent for both bottles which you find in the pictures.

The bottles to be labeled are white. See the attachment for a photo of the bottles.

The photo must also appear on the label to identify the product's intended use.

Product information:
Brand: Vorlix
Product: Sanitary Cleaner

This text must be placed on the label:
"Cleans, descales & freshens. followed with this text: "Ideal for quick and powerful cleaning. A ready-to-use product for everyday use."

- Mention the seperate USP's: Sanitary, Bathroom, Toilet, Wet areas

Appearance: This is a consumer product, but it must have a professional appearance. We would like to see a design that use the color blue from our logo.

Target Market(s)

Consumers who take care of their homes and want to maintain it the correct (professional) way

Font styles to use
Sans Serif

Colors
0054AA
0677BA
7BADD7
CADEEF
E8F1F8

Requirements
Must have
• USP's + use of image and logo + blend in 1 design
Nice to have
• Keep the color of the logo in the design
Should not have
• Comic sans

```html
<!DOCTYPE html>
<html lang="en">
<head>
<meta charset="utf-8">
<title>Vorlix Sanitary Cleaner – Label Sizes</title>
<link href="https://fonts.googleapis.com/css2?family=Montserrat:wght@400;500;600;700;800;900&display=swap" rel="stylesheet">
<style>
  :root {
    --backdrop: #8e92ad;
    --measure: #a6e02a;
    --blue-deep: #0054aa;
    --blue-mid: #0677ba;
    --blue-frame: #1d5cb8;
    --cyan: #19d4f0;
    --ink: #1a1a1a;
    --white: #ffffff;
    --photo-light: #e6e8ec;
    --photo-dark: #5b5b5c;
  }
  * { box-sizing: border-box; margin: 0; padding: 0; }
  html, body { width: 742px; height: 1200px; overflow: hidden; }
  body {
    position: relative;
    background: var(--backdrop);
    font-family: "Montserrat", sans-serif;
  }

  /* size annotations */
  .size-title {
    position: absolute; transform: translateX(-50%);
    text-align: center; font-weight: 800; font-size: 13px; color: #111;
    line-height: 1.1; white-space: nowrap;
  }
  .size-title span { display: block; font-weight: 400; font-size: 11px; color: var(--measure); }
  .measure-h, .measure-v { position: absolute; background: var(--measure); }
  .measure-h { height: 1px; }
  .measure-v { width: 1px; }
  .measure-h::before, .measure-h::after, .measure-v::before, .measure-v::after {
    content: ""; position: absolute; width: 0; height: 0;
  }
  .measure-h::before { left: 0; top: -3px; border: 3px solid transparent; border-left: 0; border-right: 6px solid var(--measure); }
  .measure-h::after { right: 0; top: -3px; border: 3px solid transparent; border-right: 0; border-left: 6px solid var(--measure); }
  .measure-v::before { top: 0; left: -3px; border: 3px solid transparent; border-top: 0; border-bottom: 6px solid var(--measure); }
  .measure-v::after { bottom: 0; left: -3px; border: 3px solid transparent; border-bottom: 0; border-top: 6px solid var(--measure); }
  .measure-label {
    position: absolute; font-size: 11px; color: var(--measure);
    transform: translate(-50%, -50%) rotate(-90deg); white-space: nowrap;
  }

  /* label */
  .label {
    position: absolute;
    display: flex; flex-direction: column;
    padding: 0.8em 0.8em 0.9em;
    background: linear-gradient(180deg, var(--blue-frame), var(--blue-deep));
    border-radius: 50% 50% 0 0 / 2.2em 2.2em 0 0;
    text-align: center;
    overflow: hidden;
  }
  .label--500 { font-size: 10px; left: 75px; top: 319px; width: 249px; height: 494px; }
  .label--1l { font-size: 12.6px; left: 377px; top: 319px; width: 314px; height: 604px; }
  .label::before {
    content: ""; position: absolute; left: 12%; right: 12%; top: 0.05em; height: 0.5em;
    background: linear-gradient(90deg, transparent, var(--cyan), transparent);
    border-radius: 50%; opacity: .8;
  }
  .label::after {
    content: ""; position: absolute; left: 0; right: 0; bottom: 0; height: 0.9em;
    background: linear-gradient(90deg, var(--blue-frame), var(--cyan) 55%, var(--blue-frame));
  }

  .label-header {
    flex: 0 0 16.6em;
    background: var(--white);
    border-radius: 50% 50% 0 0 / 1.8em 1.8em 0 0;
    padding-top: 2.1em;
    display: flex; flex-direction: column; align-items: center;
  }
  .brand { display: flex; flex-direction: column; align-items: center; gap: 0.15em; }
  .brand-mark {
    width: 3em; height: 3em; border-radius: 50%;
    border: 0.35em solid var(--blue-mid);
  }
  .brand-name { font-weight: 800; font-size: 1.45em; color: var(--ink); line-height: 1; letter-spacing: -0.01em; }
  .product-title {
    margin-top: 0.55em;
    font-weight: 900; font-size: 3.35em; line-height: 0.98; letter-spacing: -0.01em;
    text-transform: uppercase;
    background: linear-gradient(180deg, var(--cyan) 0%, var(--blue-mid) 45%, var(--blue-deep) 100%);
    -webkit-background-clip: text; background-clip: text; color: transparent;
  }

  .band {
    flex: 0 0 1em;
    background: linear-gradient(90deg, var(--blue-frame), var(--cyan) 50%, var(--blue-frame));
  }
  .usage-photo {
    flex: 1 1 auto;
    min-height: 0;
    background: linear-gradient(90deg, var(--photo-dark) 0%, #7a7874 30%, var(--photo-light) 55%, #cfd1d6 80%, #6a6b6e 100%);
  }

  .label-info {
    flex: 0 0 14.8em;
    background: var(--white);
    padding: 1.6em 0.4em 1.8em;
    display: flex; flex-direction: column; align-items: center;
  }
  .claim {
    font-weight: 700; font-size: 1.08em; line-height: 1.2;
    color: var(--ink); white-space: nowrap;
  }
  .usp-list { display: flex; justify-content: center; gap: 1.3em; margin-top: 1.1em; list-style: none; }
  .usp { display: flex; flex-direction: column; align-items: center; gap: 0.2em; }
  .usp svg { width: 2.6em; height: 2.6em; fill: var(--blue-frame); }
  .usp-name { font-size: 0.75em; color: var(--blue-frame); text-transform: uppercase; white-space: nowrap; }
  .usage-note { margin-top: 1.3em; font-size: 0.92em; line-height: 1.35; color: var(--ink); white-space: nowrap; }
</style>
</head>
<body>

  <!-- 500 ml sizing -->
  <div class="size-title" style="left:199px; top:275px;">500ml bottle<span>58mm</span></div>
  <div class="measure-h" style="left:75px; top:309px; width:249px;"></div>
  <div class="measure-v" style="left:65px; top:319px; height:494px;"></div>
  <div class="measure-label" style="left:56px; top:566px;">115 mm</div>

  <!-- 1 L sizing -->
  <div class="size-title" style="left:534px; top:275px;">1L bottle<span>73mm</span></div>
  <div class="measure-h" style="left:377px; top:309px; width:314px;"></div>
  <div class="measure-v" style="left:367px; top:319px; height:604px;"></div>
  <div class="measure-label" style="left:357px; top:621px;">140 mm</div>

  <svg width="0" height="0" style="position:absolute">
    <defs>
      <symbol id="icon-toilet" viewBox="0 0 24 24"><rect x="6" y="2" width="12" height="5" rx="1"/><path d="M4 8h16v2a8 8 0 0 1-6 6l1 6H9l1-6a8 8 0 0 1-6-6z"/></symbol>
      <symbol id="icon-bath" viewBox="0 0 24 24"><path d="M5 4a2 2 0 0 1 4 0v1H7.6V4a.6.6 0 0 0-1.2 0v8H2v2h20v-2H7.8zM3 15h18l-2 4H5z"/><rect x="5" y="19" width="2" height="3"/><rect x="17" y="19" width="2" height="3"/></symbol>
      <symbol id="icon-shower" viewBox="0 0 24 24"><path d="M18 22V5a2 2 0 0 0-4 0v1h-1.5V5a3.5 3.5 0 0 1 7 0v17z"/><path d="M7 9a5 5 0 0 1 10 0z"/><rect x="6" y="11" width="1.4" height="2"/><rect x="9" y="11" width="1.4" height="2"/><rect x="12" y="11" width="1.4" height="2"/><rect x="15" y="11" width="1.4" height="2"/><rect x="5" y="15" width="1.4" height="2"/><rect x="8.5" y="15" width="1.4" height="2"/><rect x="12" y="15" width="1.4" height="2"/><rect x="15.5" y="15" width="1.4" height="2"/><rect x="6" y="19" width="1.4" height="2"/><rect x="10" y="19" width="1.4" height="2"/><rect x="14" y="19" width="1.4" height="2"/></symbol>
      <symbol id="icon-mop" viewBox="0 0 24 24"><path d="M19 1l1.6.8-6.2 11.5-1.6-.8z"/><path d="M11 12l5 2.5-1 2.3c-1 2.5-4 4.7-8 5L5 21.5c2.5-1.3 3.8-3 4.5-4.5z"/><circle cx="5" cy="13" r="1"/><circle cx="7.5" cy="10" r=".8"/></symbol>
    </defs>
  </svg>

  <!-- 500 ml label -->
  <article class="label label--500">
    <header class="label-header">
      <div class="brand"><span class="brand-mark"></span><span class="brand-name">vorlix</span></div>
      <h1 class="product-title">Sanitary<br>Cleaner</h1>
    </header>
    <div class="band"></div>
    <div class="usage-photo" role="img" aria-label="Photo of a clean modern bathroom with walk-in shower, washbasin and tiled bathtub"></div>
    <div class="band"></div>
    <section class="label-info">
      <p class="claim">CLEANS, DESCALES &amp; FRESHENS</p>
      <ul class="usp-list">
        <li class="usp"><svg><use href="#icon-toilet"/></svg><span class="usp-name">Sanitary</span></li>
        <li class="usp"><svg><use href="#icon-bath"/></svg><span class="usp-name">Bathroom</span></li>
        <li class="usp"><svg><use href="#icon-shower"/></svg><span class="usp-name">Toilet</span></li>
        <li class="usp"><svg><use href="#icon-mop"/></svg><span class="usp-name">Wet areas</span></li>
      </ul>
      <p class="usage-note">Ideal for quick and powerful cleaning.<br>A ready-to-use product for everyday use.</p>
    </section>
  </article>

  <!-- 1 L label -->
  <article class="label label--1l">
    <header class="label-header">
      <div class="brand"><span class="brand-mark"></span><span class="brand-name">vorlix</span></div>
      <h1 class="product-title">Sanitary<br>Cleaner</h1>
    </header>
    <div class="band"></div>
    <div class="usage-photo" role="img" aria-label="Photo of a clean modern bathroom with walk-in shower, washbasin and tiled bathtub"></div>
    <div class="band"></div>
    <section class="label-info">
      <p class="claim">CLEANS, DESCALES &amp; FRESHENS</p>
      <ul class="usp-list">
        <li class="usp"><svg><use href="#icon-toilet"/></svg><span class="usp-name">Sanitary</span></li>
        <li class="usp"><svg><use href="#icon-bath"/></svg><span class="usp-name">Bathroom</span></li>
        <li class="usp"><svg><use href="#icon-shower"/></svg><span class="usp-name">Toilet</span></li>
        <li class="usp"><svg><use href="#icon-mop"/></svg><span class="usp-name">Wet areas</span></li>
      </ul>
      <p class="usage-note">Ideal for quick and powerful cleaning.<br>A ready-to-use product for everyday use.</p>
    </section>
  </article>

</body>
</html>
```